Business Card Design

We are a company that provides stump grinding services for residential and commercial clients. Looking for a simple business card design that may have some type of graphic on the card that will tie in with the Tamsen name(Grizzly Bear, Paw Print, etc) . Possibly some foliage wrapping around part of the card? Would like to have a simple design that stands out because it is unique. We are working on getting the website set up and there is a simple graphic on the top of the page that came to mind when I mentioned the leaves.

Industry/Entity Type

Business

Contact Information for Business Card

Tamsen Stump Grinding 303-257-4788KodiakStumps.Com

Font styles to use
Serif

Requirements
Must have
• Business name
• Website Address
• Phone Number
Nice to have
• Graphics that would be associated with a Tamsen bear.
Should not have
• Nothing frilly

```html
<!DOCTYPE html>
<html lang="en">
<head>
<meta charset="utf-8">
<title>Tamsen Stump Grinding – Business Card</title>
<link rel="stylesheet" href="https://fonts.googleapis.com/css2?family=Cinzel:wght@400;700&display=swap">
<style>
  :root {
    --page-bg: #2a2a2a;
    --card-bg: #ffffff;
    --ink: #0d0d0d;
    --band-text: #ffffff;
  }
  html, body {
    margin: 0;
    padding: 0;
    width: 1200px;
    height: 900px;
    overflow: hidden;
    background: var(--page-bg);
  }
  .canvas {
    position: relative;
    width: 1200px;
    height: 900px;
  }
  .business-card {
    position: absolute;
    left: 100px;
    top: 164px;
    width: 1000px;
    height: 572px;
    background: var(--card-bg);
    box-shadow: 0 10px 30px rgba(0,0,0,0.45);
  }
  .card-frame {
    position: absolute;
    inset: 28px;
    border: 2px solid var(--ink);
  }
  .brand {
    position: absolute;
    left: 300px;
    top: 118px;
    display: flex;
    align-items: center;
    gap: 22px;
  }
  .brand-mark {
    width: 190px;
    height: 190px;
    flex: none;
  }
  .brand-name {
    font-family: "Cinzel", serif;
    font-weight: 700;
    color: var(--ink);
    line-height: 1;
    margin: 0;
  }
  .brand-name .primary {
    display: block;
    font-size: 60px;
    letter-spacing: 6px;
  }
  .brand-name .secondary {
    display: block;
    font-size: 27px;
    letter-spacing: 1px;
    margin-top: 6px;
  }
  .contact-band {
    position: absolute;
    left: 50px;
    right: 50px;
    top: 452px;
    height: 46px;
    background: var(--ink);
    display: flex;
    justify-content: space-around;
    align-items: center;
    font-family: "Cinzel", serif;
    font-weight: 400;
    font-size: 20px;
    letter-spacing: 2px;
    color: var(--band-text);
  }
</style>
</head>
<body>
<div class="canvas">
  <div class="business-card">
    <div class="card-frame"></div>
    <div class="brand">
      <svg class="brand-mark" viewBox="0 0 190 190" aria-hidden="true">
        <circle cx="95" cy="95" r="95" fill="var(--ink)"/>
      </svg>
      <h1 class="brand-name">
        <span class="primary">Tamsen</span>
        <span class="secondary">Stump Grinding</span>
      </h1>
    </div>
    <div class="contact-band">
      <span class="contact-phone">Phone : 303-555-0146</span>
      <span class="contact-web">Email : TamsenStumps.Com</span>
    </div>
  </div>
</div>
</body>
</html>
```